Stationery Set for Velmora Company

I need to create full stationery design for my company; Business Cards, Envelops, Letter Heads, Calendar.
In the letter head and Envelops... only contact information and website links.
Our company is a Service Management company with different domains of innovative services including Technology Service Management, Education Services, Outsourcing Management, Events Management.
I need a modern and innovative design specially for the business card. I some transparent designs and I like it, but don't limit your innovation to what I mentioned. Sky is limit for your innovation.

Target Market(s)

Middle East & Africa

Industry/Entity Type

Business Management

Colors
34a7d8
0355a3
85acd3
86cae7
cee9f5
cfdeed
e4daeb
f3f1f8
ecf7fb

Requirements
Must have
• Name, Title, Email, Mobile
Nice to have
• We have multiple locations in USA, KSA, EGY, so I need ideas about how to include all contact details maybe QR / Barcode or something else.
• Please see our locations and contact information: www.brightvelmora.example
Should not have
• Too much text

```html
<!DOCTYPE html>
<html lang="en">
<head>
<meta charset="utf-8">
<title>Velmora Company Stationery</title>
<link rel="stylesheet" href="https://fonts.googleapis.com/css2?family=Arimo:wght@400;700&display=swap">
<style>
:root{
  --bg:#f2f2f2;
  --paper:#ffffff;
  --edge:#e2e2e2;
  --brand:#3a63d6;
  --band-dark:#2c3ca3;
  --band-light:#1e9be6;
  --ink:#333333;
  --muted:#666666;
}
*{margin:0;padding:0;box-sizing:border-box}
html,body{width:1200px;height:937px;overflow:hidden;background:var(--bg);font-family:"Arimo",Arial,sans-serif;color:var(--ink)}
.canvas{position:relative;width:1200px;height:937px}
.sheet{position:absolute;background:var(--paper);border:1px solid var(--edge);overflow:hidden}
address{font-style:normal}
.band{position:absolute;left:0;right:0;bottom:0;background:linear-gradient(90deg,var(--band-dark),var(--band-light) 70%,var(--band-dark));color:#fff;text-align:center;letter-spacing:3px;font-size:10px;display:flex;align-items:center;justify-content:center}
.band::before{content:"";position:absolute;left:0;right:0;top:-4px;height:1px;background:var(--band-dark)}
.brand{color:var(--brand);font-weight:700;white-space:nowrap;display:flex;align-items:center;gap:5px}
.brand .dot{display:inline-block;border-radius:50%;background:var(--brand)}

.letterhead{left:185px;top:68px;width:388px;height:544px}
.letterhead .brand{position:absolute;left:18px;top:26px;font-size:15px}
.letterhead .brand .dot{width:9px;height:9px}
.letterhead .contact{position:absolute;right:18px;top:24px;text-align:right;font-size:5.5px;line-height:7.5px;color:var(--muted)}
.letterhead .body{position:absolute;left:36px;top:138px;width:292px;font-size:5.3px;line-height:7.4px;color:var(--ink)}
.letterhead .body p{margin-bottom:9px}
.letterhead .body .gap{margin-bottom:20px}
.letterhead .sign{display:block;width:28px;height:16px;margin:2px 0 4px}
.letterhead .band{height:24px}

.letter-back{left:636px;top:40px;width:458px;height:577px}
.letter-back .brand{position:absolute;left:50%;top:292px;transform:translateX(-50%);font-size:28px}
.letter-back .brand .dot{width:16px;height:16px}
.letter-back .band{height:26px}

.card{width:177px;height:102px}
.card-front{left:45px;top:658px}
.card-front .brand{position:absolute;left:7px;top:12px;font-size:10px}
.card-front .brand .dot{width:6px;height:6px}
.card-front .lines{position:absolute;left:7px;top:67px;font-size:4.4px;line-height:6px;color:var(--muted)}
.card-front .person{position:absolute;right:7px;top:72px;text-align:right;font-size:7px;font-weight:700}
.card-front .person span{display:block;font-weight:400;font-size:6px;color:var(--muted)}
.card-front .band{height:10px;font-size:5px;letter-spacing:1.5px}
.card-back{left:45px;top:785px;height:100px}
.card-back .brand{position:absolute;left:50%;top:42px;transform:translateX(-50%);font-size:11px}
.card-back .brand .dot{width:6px;height:6px}

.envelope{left:265px;top:672px;width:431px;height:208px}
.envelope .brand{position:absolute;left:14px;top:26px;font-size:13px}
.envelope .brand .dot{width:8px;height:8px}
.envelope .band{height:23px;font-size:9px}

.envelope-back{left:737px;top:672px;width:415px;height:208px}
.envelope-back svg{position:absolute;left:0;top:0}
.envelope-back .flap-url{position:absolute;left:0;right:0;top:31px;text-align:center;color:#fff;font-size:10px;letter-spacing:3px}
</style>
</head>
<body>
<main class="canvas">

  <section class="sheet letterhead" aria-label="Letterhead">
    <div class="brand"><span class="dot"></span>Velmora Company</div>
    <address class="contact">1200 Harbor Line Rd<br>Dallas TX 75201<br>214.555.0148<br>lena@velmora.example</address>
    <div class="body">
      <p>July 2, 2012</p>
      <p><b>Dear Client,</b><br>ABC Building, def St., Country Name</p>
      <p>is simply dummy text of the printing and typesetting industry. Lorem Ipsum has been the industry's standard dummy text ever since the 1500s, when an unknown printer took a galley of type and scrambled it to make a type specimen book. It has survived not only five centuries, but also the leap into electronic typesetting, remaining essentially unchanged. It was popularised in the 1960s with the release of Typeleaf sheets containing Lorem Ipsum passages, and more recently with desktop publishing software like Pagecraft Studio including versions of Lorem Ipsum.</p>
      <p class="gap">is simply dummy text of the printing and typesetting industry. Lorem Ipsum has been the industry's standard dummy text ever since the 1500s, when an unknown printer took a galley of type and scrambled it to make</p>
      <p>is simply dummy text of the printing and typesetting industry. Lorem Ipsum has been the industry's standard dummy text ever since the 1500s, when an unknown printer took a galley of type and scrambled it to make a type specimen book. It has survived not only five centuries, but also the leap into electronic typesetting, remaining essentially unchanged. It was popularised in the 1960s with the release of Typeleaf sheets containing Lorem Ipsum passages, and more recently with desktop publishing software like Pagecraft Studio including versions of Lorem Ipsum.</p>
      <p>Best Regards,</p>
      <svg class="sign" viewBox="0 0 28 16" aria-hidden="true"><path d="M2 12 C6 2,8 2,7 12 S14 6,16 10 S22 8,26 10" fill="none" stroke="#222" stroke-width="0.8"/></svg>
      <p><b>Adam Reyes</b><br>Director<br><br>ABC Building, def St., Country Name</p>
    </div>
    <div class="band">www.brightvelmora.example</div>
  </section>

  <section class="sheet letter-back" aria-label="Letterhead reverse">
    <div class="brand"><span class="dot"></span>Velmora Company</div>
    <div class="band">www.brightvelmora.example</div>
  </section>

  <section class="sheet card card-front" aria-label="Business card front">
    <div class="brand"><span class="dot"></span>Velmora Company</div>
    <address class="lines">214.555.0148<br>lena@velmora.example<br>1200 Harbor Line Rd Dallas TX 75201</address>
    <div class="person">Lena Harwood<span>Owner</span></div>
    <div class="band">www.brightvelmora.example</div>
  </section>

  <section class="sheet card card-back" aria-label="Business card back">
    <div class="brand"><span class="dot"></span>Velmora Company</div>
  </section>

  <section class="sheet envelope" aria-label="Envelope front">
    <div class="brand"><span class="dot"></span>Velmora Company</div>
    <div class="band">www.brightvelmora.example</div>
  </section>

  <section class="sheet envelope-back" aria-label="Envelope back">
    <svg width="415" height="208" viewBox="0 0 415 208" aria-hidden="true">
      <defs>
        <linearGradient id="flapFill" x1="0" x2="1" y1="0" y2="0">
          <stop offset="0" stop-color="#2c3ca3"/>
          <stop offset="0.6" stop-color="#1e9be6"/>
          <stop offset="1" stop-color="#2c3ca3"/>
        </linearGradient>
      </defs>
      <path d="M0 0 H415 V40 Q415 72 383 72 H32 Q0 72 0 40 Z" fill="url(#flapFill)"/>
    </svg>
    <div class="flap-url">www.brightvelmora.example</div>
  </section>

</main>
</body>
</html>
```